Business card

We need a business card design for our company based in Auckland , New Zealand called 'Ridge + Studio Ltd'. We provide architectural services. We would like to see designs that use the max. three colours (such as white, black, grey) The final design should communicate financial safety and growth."
Also I will provide our company logo. I would like to the logo to be embeded onto our business card.

Target Market(s)

new residential house, alteration & addition & light commericila design & drafting service

Industry/Entity Type

Architecture

Contact Information for Business Card

Company name: ridge + studio Ltd.
Name: Mark Delford
Job title: architectural designer & Design RDL
email address: mark@rplusd.co.nz
mobile number: 02 5163 2290
web site: www.rplusd.co.nz

Requirements
Must have
• My project must have..
• - embeded logo (attached company logo)
• I don't have a bigger version for our company logo, but I have one old one, so you can remove the word from it)
• - insert the attached small BKTW logo & LBP logo
• - creative, simple and clear business card.
• - Max. three colours
Nice to have
• - Here are the samples I would like to share with you: http://www.plimvora.com/blog/minimalistic-business-card-designs/
• I would like to have my business card like one of the creation.
Should not have
• TBA

```html
<!DOCTYPE html>
<html lang="en">
<head>
<meta charset="utf-8">
<title>Ridge + Studio Ltd. — Business Card</title>
<link rel="stylesheet" href="https://fonts.googleapis.com/css2?family=Open+Sans:wght@400;600&family=Roboto:wght@400;500&display=swap">
<style>
  :root {
    --page: #e9e7e4;
    --card-light: #f4f3f1;
    --card-dark: #000000;
    --ink: #111111;
    --paper-text: #ffffff;
    --mute: #8a8a8a;
    --faint: #c9c9c9;
    --badge-grey: #5f5f5f;
  }
  * { margin: 0; padding: 0; box-sizing: border-box; }
  html, body { width: 1200px; height: 900px; overflow: hidden; }
  body {
    background: var(--page);
    font-family: "Open Sans", Arial, sans-serif;
    position: relative;
  }
  .card {
    position: absolute;
    width: 556px;
    height: 345px;
    overflow: hidden;
    box-shadow: 0 6px 22px rgba(0,0,0,0.12);
  }
  .card--front { left: 238px; top: 60px; }
  .card--back { left: 458px; top: 518px; width: 560px; height: 344px; }

  .card__top {
    position: absolute; left: 0; top: 0; right: 0;
    height: 187px;
    background: var(--card-light);
  }
  .card__band {
    position: absolute; left: 0; right: 0; bottom: 0;
    height: 158px;
    background: var(--card-dark);
  }

  .brand { position: absolute; left: 0; right: 0; text-align: center; }
  .brand__dot {
    position: absolute; left: 50%; top: 18px;
    width: 118px; height: 118px; margin-left: -59px;
    border-radius: 50%;
    border: 6px solid var(--ink);
  }
  .brand__name {
    position: absolute; left: 0; right: 0; top: 146px;
    font-family: "Roboto", Arial, sans-serif;
    font-size: 22px; font-weight: 500; color: var(--ink);
    line-height: 30px;
  }

  .brand--faint .brand__dot { border-color: var(--faint); }
  .brand--faint .brand__name {
    color: var(--mute); opacity: 0.75;
    transform: scaleX(-1);
  }

  .person {
    position: absolute; right: 242px; top: 244px;
    text-align: right; color: var(--paper-text);
  }
  .person__name { font-size: 18px; font-weight: 600; line-height: 24px; }
  .person__role { font-size: 15px; line-height: 20px; }

  .contacts {
    position: absolute; left: 344px; top: 236px;
    list-style: none; color: var(--paper-text);
    font-size: 14.5px; line-height: 20px;
  }
  .contacts li { display: flex; align-items: center; gap: 9px; }
  .contacts svg { width: 11px; height: 11px; fill: var(--paper-text); flex: none; }

  .badge { position: absolute; }
  .badge--member {
    left: 152px; top: 222px; width: 124px; height: 92px;
    background: var(--badge-grey);
  }
  .badge--licence {
    left: 296px; top: 214px; width: 112px; height: 112px;
    border-radius: 50%;
    background: var(--paper-text);
    border: 6px solid var(--badge-grey);
  }
</style>
</head>
<body>

  <section class="card card--front" aria-label="Business card front">
    <div class="card__top">
      <div class="brand">
        <span class="brand__dot"></span>
        <p class="brand__name">Ridge + Studio Ltd.</p>
      </div>
    </div>
    <div class="card__band"></div>

    <div class="person">
      <p class="person__name">Mark Delford</p>
      <p class="person__role">Architectural designer &amp; Design RDL</p>
    </div>

    <ul class="contacts">
      <li>
        <svg viewBox="0 0 24 24" aria-hidden="true"><path d="M6.6 10.8a15.1 15.1 0 0 0 6.6 6.6l2.2-2.2a1 1 0 0 1 1-.25 11.4 11.4 0 0 0 3.6.57 1 1 0 0 1 1 1V20a1 1 0 0 1-1 1A17 17 0 0 1 3 4a1 1 0 0 1 1-1h3.5a1 1 0 0 1 1 1c0 1.25.2 2.45.57 3.6a1 1 0 0 1-.25 1z"/></svg>
        <span>02 5163 2290</span>
      </li>
      <li>
        <svg viewBox="0 0 24 24" aria-hidden="true"><path d="M2 5h20v2l-10 6L2 7z"/><path d="M2 9l10 6 10-6v10H2z"/></svg>
        <span>mark@rplusd.co.nz</span>
      </li>
      <li>
        <svg viewBox="0 0 24 24" aria-hidden="true"><circle cx="12" cy="12" r="11"/><path d="M12 1v22M1 12h22" stroke="#000" stroke-width="1.5" fill="none"/></svg>
        <span>www.rplusd.co.nz</span>
      </li>
    </ul>
  </section>

  <section class="card card--back" aria-label="Business card back">
    <div class="card__top">
      <div class="brand brand--faint">
        <span class="brand__dot"></span>
        <p class="brand__name">Ridge + Studio Ltd.</p>
      </div>
    </div>
    <div class="card__band"></div>

    <div class="badge badge--member" role="img" aria-label="BKTW professional membership badge"></div>
    <div class="badge badge--licence" role="img" aria-label="Registered design licence seal"></div>
  </section>

</body>
</html>
```